Interior Plaster, Plasterboard Fixing & Installation Business CardDesign

BRANVO The name was formed by me, in talking to my accountant, whilst skim coating his walls and I had seen an imperfection in a wall that needed to be skim coated to deflect the light from the imperfection. I responded to him saying...."just Bran Vo". The idea originates from the process of applying a skim coat of interior plaster to a wall to achieve a smoother surface. This is required prior to many applications, applying wall paper, preparation for paint, after removing wall paper, improving aesthetics, joints that have not been properly jointed etc. Different types of light reflected on the surface, makes poor jointing more visible. In addition, the businesses key functions will be interior plastering, plaster board installation (ceilings and walls) and plasterboard jointing to a level that is prepared for a painter. Once the plaster is applied the surface requires sanding using different types of sanding equipment manual and electronic, including the use of specialised paint-on sealers for the surface. I believe the name is simple, easy to remember, but may be read incorrectly. I have had people ask if it was Bran Vo, referring to information technology.

For now, this entire concept is driven by passion and started 2 years ago whilst renovating my own home.

I need to be able to use your expertise to translate my ideas, starting with business card and progressing to a website incorporating anything and everything in between. The final design should be easy to understand, read and standout with an element of uniqueness. Humour maybe an option, or the idea of leaving a prospect with something that is thought provoking.
Updates

Hi All Ideas look fine so far, but would expect to see different colour options. I am thinking plaster thats cream in colour, so more earthy colour on the card. A picture of a trowel to replace the I in BRANVO maybe. I like the swirl that is created by a notched trowel moving through plaster. Perhaps a more modern or fresher look. With BRANVO, could you consider reversing the direction of the K for instance facing in the opposite direction. In saying this I look to you for your experience and expertise with the idea. The other option with the K, could be to remove the first straight line, i hope that my explanation helps. Sorry if it doesn't. Thanks heaps :)

Please include the type of service. Plasterboard Services

I have considered the idea of the K being reversed, and I am of the view that it presents a challenge reading and understanding. Moving forward I would however like to use the K in the normal direction but without the first straight line. I need to see more colour options that are grey or earthy. Can a picture of a trowel be included if it makes sense and with that tool being frequently used in plastering.

Industry/Entity Type

Business

Contact Information for Business Card

Company name: BranVo
Name: Dorian Pekke
Title: Director
Email address: pekkedp@mailvora.example
Mobile number: 0210 481 7092
Address: 17 Tamsin Lane, Glenfield, Auckland, 0629

```html
<!DOCTYPE html>
<html lang="en">
<head>
<meta charset="utf-8">
<title>BranVo – Business Card</title>
<link rel="stylesheet" href="https://fonts.googleapis.com/css2?family=Marcellus+SC&display=swap">
<style>
  :root {
    --bg: #e9eaec;
    --card: #ffffff;
    --card-shade: #f1f2f4;
    --blue-deep: #1360c4;
    --blue-mid: #2a85e2;
    --blue-light: #5fb1f2;
    --swoosh: #a3a6ab;
    --brand: #1d5fbf;
    --ink-light: #ffffff;
    --font: "Marcellus SC", "Times New Roman", serif;
  }
  * { box-sizing: border-box; margin: 0; padding: 0; }
  html, body {
    width: 1200px; height: 900px; overflow: hidden;
    background: var(--bg);
    font-family: var(--font);
  }
  .sheet {
    width: 1200px; height: 900px;
    display: flex; align-items: center; justify-content: center; gap: 40px;
  }
  .card {
    position: relative;
    width: 540px; height: 310px;
    border-radius: 34px;
    overflow: hidden;
    background: linear-gradient(180deg, var(--card) 0%, var(--card-shade) 100%);
    box-shadow: 0 6px 18px rgba(0,0,0,0.12);
  }
  .card-wave { position: absolute; inset: 0; width: 100%; height: 100%; }
  .brand-name {
    position: absolute;
    font-family: var(--font);
    color: var(--brand);
    letter-spacing: 2px;
    line-height: 1;
  }
  .card-front .brand-name { top: 34px; left: 0; right: 0; text-align: center; font-size: 46px; padding-left: 60px; }
  .card-back .brand-name { top: 118px; left: 0; right: 0; text-align: center; font-size: 58px; }

  .holder {
    position: absolute; top: 168px; right: 282px;
    text-align: right; color: var(--ink-light);
  }
  .holder-name { font-size: 17px; letter-spacing: 1.5px; }
  .holder-title { font-size: 10.5px; letter-spacing: 1px; margin-top: 3px; opacity: 0.9; }
  .holder-service { font-size: 9.5px; letter-spacing: 1px; margin-top: 2px; opacity: 0.9; }
  .address {
    position: absolute; top: 228px; right: 282px;
    text-align: right; color: var(--ink-light);
    font-size: 10px; letter-spacing: 1px; line-height: 1.45;
  }
  .contact-list {
    position: absolute; top: 176px; left: 276px;
    list-style: none; color: var(--ink-light);
    font-size: 10.5px; letter-spacing: 1px;
  }
  .contact-list li { display: flex; align-items: center; gap: 7px; height: 19px; }
  .contact-icon { width: 12px; height: 12px; flex: none; }
</style>
</head>
<body>
<main class="sheet">

  <section class="card card-front" aria-label="Business card front">
    <svg class="card-wave" viewBox="0 0 540 310" preserveAspectRatio="none" aria-hidden="true">
      <defs>
        <linearGradient id="blueField" x1="0" y1="0" x2="1" y2="1">
          <stop offset="0" stop-color="var(--blue-deep)"/>
          <stop offset="0.55" stop-color="var(--blue-mid)"/>
          <stop offset="1" stop-color="var(--blue-light)"/>
        </linearGradient>
      </defs>
      <path d="M0 95 C120 70 200 110 290 150 C380 190 460 175 540 150 L540 165 C460 192 380 205 290 168 C200 128 120 92 0 112 Z" fill="var(--swoosh)"/>
      <path d="M0 112 C120 92 200 128 290 168 C380 205 460 192 540 165 L540 310 L0 310 Z" fill="url(#blueField)"/>
    </svg>

    <div class="brand-name">BranVo</div>

    <div class="holder">
      <div class="holder-name">Dorian Pekke</div>
      <div class="holder-title">Director</div>
      <div class="holder-service">Plasterboard Services</div>
    </div>
    <div class="address">17 Tamsin Lane,<br>Glenfield,<br>Auckland, 0629</div>

    <ul class="contact-list">
      <li>
        <svg class="contact-icon" viewBox="0 0 12 12"><circle cx="6" cy="6" r="6" fill="#fff"/><path d="M4 3h1.4l.6 1.6-.8.6a4 4 0 0 0 1.6 1.6l.6-.8 1.6.6V8a1 1 0 0 1-1 1A5 5 0 0 1 3 4a1 1 0 0 1 1-1z" fill="var(--blue-deep)"/></svg>
        0210 481 7092
      </li>
      <li>
        <svg class="contact-icon" viewBox="0 0 12 12"><circle cx="6" cy="6" r="6" fill="#fff"/><rect x="4" y="2.5" width="4" height="7" rx="0.8" fill="var(--blue-deep)"/></svg>
        09 482 6130
      </li>
      <li>
        <svg class="contact-icon" viewBox="0 0 12 12"><circle cx="6" cy="6" r="6" fill="#fff"/><rect x="3" y="4.5" width="6" height="3.5" rx="0.5" fill="var(--blue-deep)"/><rect x="4" y="2.8" width="4" height="1.5" fill="var(--blue-deep)"/></svg>
        09 482 6131
      </li>
      <li>
        <svg class="contact-icon" viewBox="0 0 12 12"><circle cx="6" cy="6" r="6" fill="#fff"/><rect x="3" y="3.8" width="6" height="4.4" fill="var(--blue-deep)"/><path d="M3 3.8 6 6.3 9 3.8" stroke="#fff" stroke-width="0.7" fill="none"/></svg>
        pekkedp@mailvora.example
      </li>
      <li>
        <svg class="contact-icon" viewBox="0 0 12 12"><circle cx="6" cy="6" r="6" fill="#fff"/><circle cx="6" cy="6" r="3.2" fill="none" stroke="var(--blue-deep)" stroke-width="0.8"/><path d="M2.8 6h6.4M6 2.8c-1.6 2-1.6 4.4 0 6.4M6 2.8c1.6 2 1.6 4.4 0 6.4" stroke="var(--blue-deep)" stroke-width="0.6" fill="none"/></svg>
        www.branvo.example
      </li>
    </ul>
  </section>

  <section class="card card-back" aria-label="Business card back">
    <div class="brand-name">BranVo</div>
  </section>

</main>
</body>
</html>
```